Talvoro bonds (Surety bond broker)

We are a broker of surety bonds, we need a presentation and a flyer with fresh design. Our core values are reliable, on time and customized service. We want to transmit to our clients, they can leave on us the process of underwriting and issuing a surety bond, so they can focus on their business with no distractions.

Font styles to use
Sans Serif
Other font styles liked:

Requirements
Must have
• Visually attractive.
Main Message: Fast service issuing and underwriting surety bonds, reliable, nos surprises, we are always one step ahead, customized and personalized bonding solutions.
Nice to have
• Have short version for the flyer, and extended version for the presentation.
Should not have
• We already have a logo (attached), maintain colors

```html
<!DOCTYPE html>
<html lang="es">
<head>
<meta charset="utf-8">
<title>Talvoro — Seguros y Fianzas</title>
<link href="https://fonts.googleapis.com/css2?family=Montserrat:wght@400;500;600;700&display=swap" rel="stylesheet">
<style>
:root{
  --green:#6aa842;
  --green-light:#8cc265;
  --ink:#050505;
  --paper:#ffffff;
  --stage:#3a3a3a;
  --body-dark:#d9d9d9;
  --body-light:#4a4a4a;
  --logo-grey:#333333;
}
*{margin:0;padding:0;box-sizing:border-box}
html,body{width:853px;height:1200px;overflow:hidden;background:var(--stage);font-family:"Montserrat",sans-serif}
.sheet{position:absolute;left:62.5px;width:728px;height:514px;overflow:hidden;background:var(--ink)}
.sheet--outside{top:58px}
.sheet--inside{top:631px}
.panel{position:absolute;top:0;width:242.7px;height:514px}
.panel--1{left:0}.panel--2{left:242.7px}.panel--3{left:485.3px}
.panel--light{background:var(--paper)}
.panel--dark{background:var(--ink)}
.panel--3.panel--dark{border-left:1px solid #1c1c1c}
.heading{position:absolute;font-size:16.5px;font-weight:500;line-height:1;white-space:nowrap}
.heading .accent{color:var(--green)}
.panel--light .heading{color:#111}
.panel--dark .heading{color:#fff}
.dash{position:absolute;width:12px;height:2px;background:var(--green)}
.dash--black{background:#111}
.dash--white{background:#fff}
.copy{position:absolute;font-size:7.4px;line-height:10.7px}
.copy p{margin-bottom:7.5px}
.panel--light .copy{color:var(--body-light)}
.panel--dark .copy{color:var(--body-dark)}
.copy .hl{color:var(--green)}
.photo{position:absolute;border-radius:50%}
.ring{position:absolute;border-radius:50%;border:1px solid var(--green)}
.bubble{position:absolute;border-radius:50%;background:var(--green);opacity:.55}

/* partners */
.partners-title{position:absolute;top:27px;left:0;width:242.7px;text-align:center;color:var(--green);font-size:12px;font-weight:600}
.partners-ring{left:15px;top:52px;width:208px;height:208px;z-index:3}
.partners-disc{position:absolute;left:20px;top:57px;width:198px;height:198px;border-radius:50%;background:#fff;z-index:4}
.partner{position:absolute;display:flex;align-items:center;gap:3px;color:var(--logo-grey);font-size:8.5px;font-weight:600;white-space:nowrap}
.partner .mark{width:9px;height:9px;border-radius:50%;background:var(--logo-grey);flex:none}

/* brand */
.brand{position:absolute;display:flex;align-items:center;gap:5px}
.brand .mark{border-radius:50%;border:1.5px solid var(--green);flex:none}
.brand .name{color:var(--green);font-weight:500;letter-spacing:.5px;line-height:1}
.brand-tag{position:absolute;color:#fff;font-weight:700;letter-spacing:1.6px;white-space:nowrap}

/* contact */
.contact-name{position:absolute;left:42px;color:var(--green);font-size:8.6px;font-weight:600}
.contact-line{position:absolute;left:31px;display:flex;align-items:center;gap:5px;color:#fff;font-size:8.6px;font-weight:500;white-space:nowrap}
.contact-line .ico{width:8px;height:8px;flex:none}
.green{color:var(--green)}

/* cover */
.slogan{position:absolute;left:37px;font-weight:700;line-height:1;white-space:nowrap}
.slogan--white{top:404px;color:#fff;font-size:23px}
.slogan--green{top:427px;color:var(--green);font-size:24.5px}
.cover-web{position:absolute;left:35px;top:482px;display:flex;align-items:center;gap:6px;color:#fff;font-size:10px;font-weight:500;letter-spacing:3.4px;white-space:nowrap}

/* services */
.services{position:absolute;left:27px;top:314px;width:200px;list-style:none}
.services li{position:relative;padding-left:9px;color:#fff;font-size:8px;font-weight:600;line-height:10.2px;margin-bottom:7.6px}
.services li::before{content:"✓";position:absolute;left:0;top:0;color:var(--green);font-weight:400}
.services small{display:block;font-size:4.6px;font-weight:400;color:#bbb;line-height:7px}

/* products */
.product{position:absolute;left:24px;width:78px;height:78px;border-radius:50%;background:var(--green);box-shadow:0 0 0 1.5px var(--ink),0 0 0 2.6px var(--green);display:flex;flex-direction:column;align-items:center;justify-content:center;color:#fff;font-size:7.8px;font-weight:500}
.product svg{width:28px;height:28px;margin-bottom:5px}
.items{position:absolute;left:115px;list-style:none}
.item{position:absolute;left:0;white-space:nowrap;font-size:7.6px;line-height:10px;padding-left:10px}
.item--tick{color:var(--green);font-weight:500}
.item--tick::before{content:"✓";position:absolute;left:0;color:#fff}
.item--dot{color:#ddd}
.item--dot::before{content:"";position:absolute;left:2px;top:3.5px;width:3px;height:3px;border-radius:50%;background:#fff}
.connector{position:absolute;left:0;top:0;width:242.7px;height:514px}

/* specials */
.special-title{position:absolute;left:28px;color:var(--green);font-size:10.6px;font-weight:500;line-height:12.6px}
.cta{position:absolute;left:29px;top:438px;width:193px;height:30px;background:var(--green);color:#fff;font-size:20px;font-weight:700;display:flex;align-items:center;justify-content:center;letter-spacing:.3px;white-space:nowrap}
.cta-phone{position:absolute;left:20px;top:474px;width:211px;text-align:center;color:#111;font-size:19px;font-weight:700;line-height:24px;white-space:nowrap}
</style>
</head>
<body>

<section class="sheet sheet--outside">

  <div class="panel panel--1 panel--light">
    <h2 class="heading" style="left:29px;top:26px">¿Quiénes <span class="accent">somos?</span></h2>
    <div class="dash" style="left:29px;top:52px"></div>
    <div class="copy" style="left:29px;top:66px;width:186px">
      <p>Talvoro Bonds, somos un grupo de jóvenes emprendedores, con amplia experiencia en el sector afianzador.</p>
      <p>Estamos convencidos de que nuestro principal diferenciador es la pasión por el servicio.</p>
      <p>Nuestra prioridad es el éxito de cada uno de nuestros clientes, nos aseguramos de que el “trámite” de fianzas deje de ser un “trámite” y se convierta en la llave del éxito para cada uno de nuestros fiados y beneficiarios.</p>
      <p>Buscamos siempre tener relaciones estrechas y de largo plazo con todos nuestros ”stakeholders”. Por lo que nos rodeamos del mejor talento en el sector para garantizar a nuestros clientes un servicio personalizado, en tiempo y confiable.</p>
    </div>
    <div class="ring" style="left:-24px;top:287px;width:256px;height:256px"></div>
    <div class="photo" role="img" aria-label="Fotografía de obra en construcción con grúa y trabajadores al atardecer" style="left:-31px;top:291px;width:252px;height:252px;background:linear-gradient(180deg,#7fb2dd 0%,#b9cfdf 38%,#d9b36a 60%,#7a6a5a 100%)"></div>
    <div class="bubble" style="left:127px;top:272px;width:68px;height:68px"></div>
    <div class="bubble" style="left:182px;top:324px;width:40px;height:40px"></div>
  </div>

  <div class="panel panel--2 panel--dark">
    <h2 class="partners-title">Nuestro Socios de Negocio</h2>
    <div class="ring partners-ring"></div>
    <div class="partners-disc">
      <div class="partner" style="left:62px;top:22px"><span class="mark"></span>Solvera</div>
      <div class="partner" style="left:25px;top:54px"><span class="mark"></span>Arvento</div>
      <div class="partner" style="left:107px;top:54px"><span class="mark"></span>Koru Marine</div>
      <div class="partner" style="left:25px;top:85px">Crelt</div>
      <div class="partner" style="left:104px;top:85px"><span class="mark"></span>Fianzas Domira</div>
      <div class="partner" style="left:25px;top:117px"><span class="mark"></span>Lumen Fianzas</div>
      <div class="partner" style="left:107px;top:117px">Cendral<span class="mark"></span></div>
      <div class="partner" style="left:34px;top:152px">Marvia</div>
      <div class="partner" style="left:107px;top:152px">Fianzas Altea</div>
    </div>

    <div class="brand" style="left:29px;top:277px">
      <span class="mark" style="width:14px;height:14px"></span>
      <span class="name" style="font-size:23px">TALVORO</span>
    </div>
    <div class="brand-tag" style="left:83px;top:300px;font-size:4.8px">SEGUROS Y FIANZAS</div>

    <h3 class="heading" style="left:40px;top:316px;font-size:14px">Contacto</h3>
    <div class="dash" style="left:40px;top:336px"></div>

    <div class="contact-name" style="top:350px">Lucía Paredes</div>
    <div class="contact-line" style="top:363px"><svg class="ico" viewBox="0 0 10 10"><circle cx="5" cy="5" r="4.4" fill="none" stroke="#6aa842" stroke-width=".8"/><rect x="2.8" y="3.5" width="4.4" height="3" fill="none" stroke="#6aa842" stroke-width=".6"/></svg><span>lparedes@talvoro.com</span></div>
    <div class="contact-line" style="top:376px"><svg class="ico" viewBox="0 0 10 10"><circle cx="5" cy="5" r="4.4" fill="none" stroke="#6aa842" stroke-width=".8"/><path d="M3.3 3c.3 1.8 1.5 3.2 3.4 3.8l.6-.8-1-.6-.5.4c-.7-.4-1.1-.9-1.4-1.6l.4-.5-.6-1z" fill="#6aa842"/></svg><span>55 0140 2211</span></div>
    <div class="contact-name" style="top:391px">Marta Reyes</div>
    <div class="contact-line" style="top:404px"><svg class="ico" viewBox="0 0 10 10"><circle cx="5" cy="5" r="4.4" fill="none" stroke="#6aa842" stroke-width=".8"/><rect x="2.8" y="3.5" width="4.4" height="3" fill="none" stroke="#6aa842" stroke-width=".6"/></svg><span>mreyes@talvoro.com</span></div>
    <div class="contact-line" style="top:417px"><svg class="ico" viewBox="0 0 10 10"><circle cx="5" cy="5" r="4.4" fill="none" stroke="#6aa842" stroke-width=".8"/><path d="M3.3 3c.3 1.8 1.5 3.2 3.4 3.8l.6-.8-1-.6-.5.4c-.7-.4-1.1-.9-1.4-1.6l.4-.5-.6-1z" fill="#6aa842"/></svg><span>55 0172 3344</span></div>
    <div class="contact-name" style="top:431px">Tomás Villalba</div>
    <div class="contact-line" style="top:444px"><svg class="ico" viewBox="0 0 10 10"><circle cx="5" cy="5" r="4.4" fill="none" stroke="#6aa842" stroke-width=".8"/><rect x="2.8" y="3.5" width="4.4" height="3" fill="none" stroke="#6aa842" stroke-width=".6"/></svg><span>tvillalba@talvoro.com</span></div>
    <div class="contact-line" style="top:457px"><svg class="ico" viewBox="0 0 10 10"><circle cx="5" cy="5" r="4.4" fill="none" stroke="#6aa842" stroke-width=".8"/><path d="M3.3 3c.3 1.8 1.5 3.2 3.4 3.8l.6-.8-1-.6-.5.4c-.7-.4-1.1-.9-1.4-1.6l.4-.5-.6-1z" fill="#6aa842"/></svg><span>55 0195 6677</span></div>
    <div class="contact-line" style="top:481px"><svg class="ico" viewBox="0 0 10 10"><circle cx="5" cy="5" r="4.4" fill="none" stroke="#6aa842" stroke-width=".8"/><path d="M3 7l4-4M4.5 3H7v2.5" fill="none" stroke="#6aa842" stroke-width=".7"/></svg><span>www.<span class="green">talvoro</span>.com</span></div>
  </div>

  <div class="panel panel--3 panel--dark">
    <div class="brand" style="left:30px;top:34px">
      <span class="mark" style="width:18px;height:18px"></span>
      <span class="name" style="font-size:33px">TALVORO</span>
    </div>
    <div class="brand-tag" style="left:125px;top:69px;font-size:6.6px">SEGUROS Y FIANZAS</div>

    <div class="ring" style="left:-56px;top:93px;width:289px;height:289px;border-width:1.2px"></div>
    <div class="photo" role="img" aria-label="Fotografía de un ingeniero y un supervisor con cascos revisando planos frente a un edificio" style="left:-51px;top:100px;width:276px;height:276px;background:linear-gradient(160deg,#e9edf0 0%,#c4ccd2 45%,#8a8f94 70%,#c2642c 100%)"></div>

    <div class="slogan slogan--white">Tu éxito..</div>
    <div class="slogan slogan--green">nuestra pasión</div>
    <div class="dash" style="left:37px;top:464px;width:20px;height:3px"></div>
    <div class="cover-web"><svg width="9" height="9" viewBox="0 0 10 10"><circle cx="5" cy="5" r="4.4" fill="none" stroke="#6aa842" stroke-width=".8"/><path d="M3 7l4-4M4.5 3H7v2.5" fill="none" stroke="#6aa842" stroke-width=".7"/></svg><span>www.<span class="green">talvoro</span>.com</span></div>
  </div>
</section>

<section class="sheet sheet--inside">

  <div class="panel panel--1 panel--dark">
    <h2 class="heading" style="left:27px;top:27px">Nuestra oferta <span class="accent">de valor</span></h2>
    <div class="dash dash--white" style="left:27px;top:53px"></div>
    <div class="copy" style="left:27px;top:67px;width:196px">
      <p><span class="hl">Para nuestros fiados,</span> nos aseguramos de que el proceso de emisión de fianzas sea <span class="hl">claro, rápido y sencillo.</span> Dando una asesoría personalizada y seguimiento puntual a cada solicitud.</p>
      <p>Sabemos la importancia de tener una fianza en tiempo y sin errores, por lo que nos empeñamos en siempre ir un paso adelante, permitiendo que nuestros clientes se despreocupen del proceso de afianzamiento y logren todos sus objetivos.</p>
      <p><span class="hl">Para nuestros beneficiarios,</span> trabajamos solo con las mejores afianzadoras del país y garantizamos que todos nuestros clientes cuenten con una garantía confiable, que les permita concluir sus proyectos con la tranquilidad de que tienen un respaldo confiable. Nuestro compromiso es siempre mitigar los riesgos y nunca dejar desprotegidos a nuestros clientes</p>
    </div>
    <h2 class="heading" style="left:27px;top:281px">Nuestros <span class="accent">Servicios</span></h2>
    <div class="dash dash--white" style="left:27px;top:298px"></div>
    <ul class="services">
      <li>Asesoría personalizada para la obtención de Líneas de Afianzamiento</li>
      <li>Emisión y administración de fianzas.<small>(Fidelidad, Administrativas, Judiciales, Crédito y Fideicomisos)</small></li>
      <li>Diseño, implementación y gestión de esquemas de afianzamiento.</li>
      <li>Asesoría en riesgos para contratos de obra, suministro y proveeduría.</li>
      <li>Colocación de fianzas internacionales y reaseguro.</li>
      <li>Asesoría legal en proceso de reclamación de fianzas.</li>
      <li>Esquemas de afianzamiento masivos.</li>
    </ul>
  </div>

  <div class="panel panel--2 panel--dark">
    <h2 class="heading" style="left:33px;top:27px">Productos en <span class="accent">Fianzas</span></h2>
    <div class="dash dash--white" style="left:33px;top:53px"></div>

    <svg class="connector" viewBox="0 0 242.7 514" aria-hidden="true">
      <g stroke="#ffffff" stroke-width=".8" fill="none">
        <path d="M102 114H169"/>
        <path d="M66.5 254V255.5H169"/>
        <path d="M66.5 363V389H169"/>
        <path d="M66.5 482V496H169"/>
      </g>
      <g fill="#6aa842"><circle cx="169" cy="114" r="1.6"/><circle cx="169" cy="255.5" r="1.6"/><circle cx="169" cy="389" r="1.6"/><circle cx="169" cy="496" r="1.6"/></g>
    </svg>

    <div class="product" style="top:73px">
      <svg viewBox="0 0 28 28" fill="#fff"><circle cx="15" cy="5" r="3"/><path d="M9 10l6-1 4 4 4 0v2.4l-5 0-2-2-1 5 4 3-1.2 6-2.4-.5 1-4.4-4.6-3-3 5.6-4-.2 3.6-6.4 1-4.6-2.4 1-1.2 3.4-2.2-.8z"/></svg>
      Fidelidad
    </div>
    <div class="product" style="top:176px">
      <svg viewBox="0 0 28 28" fill="#fff"><g transform="rotate(-40 14 12)"><rect x="7" y="6" width="14" height="5.5" rx="1"/><rect x="12.6" y="11" width="2.8" height="11"/></g><rect x="3" y="22" width="12" height="3" rx="1"/></svg>
      Judicial
    </div>
    <div class="product" style="top:285px">
      <svg viewBox="0 0 28 28" fill="#fff"><circle cx="12" cy="8" r="5"/><path d="M2 26c0-6 4.5-10 10-10s10 4 10 10z"/><circle cx="21" cy="20" r="5.5" stroke="#6aa842" stroke-width="1.2"/><path d="M18.5 20l2 2 3.5-3.6" stroke="#6aa842" stroke-width="1.4" fill="none"/></svg>
      Administrativas
    </div>
    <div class="product" style="top:404px">
      <svg viewBox="0 0 28 28" fill="none" stroke="#fff" stroke-width="1.4"><rect x="6" y="4" width="19" height="13" rx="1.5" transform="rotate(10 15 10)"/><rect x="2" y="9" width="20" height="14" rx="1.5" fill="#6aa842"/><path d="M2 13h20M5 19h6M13 19h3"/></svg>
      Crédito
    </div>

    <ul class="items" style="top:0">
      <li class="item item--tick" style="top:88px">Colectiva</li>
      <li class="item item--tick" style="top:100px">Individual</li>
      <li class="item item--tick" style="top:139px">Penales</li>
      <li class="item item--dot" style="top:154px">Libertad provisional</li>
      <li class="item item--dot" style="top:166px">Condena provisional</li>
      <li class="item item--dot" style="top:177px">Reparación del daño</li>
      <li class="item item--dot" style="top:189px">Sanción pecuniaria</li>
      <li class="item item--tick" style="top:205px">No Penales</li>
      <li class="item item--dot" style="top:218px">Daños y prejuicios</li>
      <li class="item item--dot" style="top:229px">Pensión alimenticia</li>
      <li class="item item--dot" style="top:240px">Laboral</li>
      <li class="item item--tick" style="top:281px">Obra y Proveeduría</li>
      <li class="item item--dot" style="top:293px">Cumplimiento</li>
      <li class="item item--dot" style="top:305px">Anticipo</li>
      <li class="item item--dot" style="top:316px">Buena Calidad</li>
      <li class="item item--dot" style="top:328px">Contingencias Laborales</li>
      <li class="item item--tick" style="top:345px">Arrendamiento</li>
      <li class="item item--tick" style="top:357px">Contingencias ambientales</li>
      <li class="item item--tick" style="top:368px">Fiscales</li>
      <li class="item item--tick" style="top:404px">Compra venta</li>
      <li class="item item--tick" style="top:415px">Suministro</li>
      <li class="item item--dot" style="top:428px">CNE</li>
      <li class="item item--dot" style="top:440px">Estaciones de Servicio</li>
      <li class="item item--dot" style="top:451px">Petronal</li>
      <li class="item item--dot" style="top:462px">Aerova</li>
      <li class="item item--tick" style="top:475px">Otras Crédito</li>
    </ul>
  </div>

  <div class="panel panel--3 panel--light">
    <h2 class="heading" style="left:28px;top:27px">Productos <span class="accent">Especiales</span></h2>
    <div class="dash dash--black" style="left:28px;top:54px"></div>

    <h3 class="special-title" style="top:73px">Flujo Garantizado</h3>
    <div class="copy" style="left:29px;top:92px;width:190px">
      <p>Es una fianza con la que se constituye un fondo colectivo para productos masivos que permite darle viabilidad financiera a tu empresa, proporcionándole el flujo constante de recursos para cubrir posibles pérdidas por quebrantos de créditos o cuentas por cobrar no liquidadas por sus clientes.</p>
    </div>

    <h3 class="special-title" style="top:188px">Esquemas de Proveedores</h3>
    <div class="copy" style="left:29px;top:206px;width:190px">
      <p>Esquema diseñado para grandes beneficiarios, que permite proteger los recursos invertidos en proyectos de construcción y adquisición de bienes o prestación de servicios, garantizando las obligaciones que se derivan de estos a cargo de sus proveedores o contratistas.</p>
      <p>Este programa permite la fácil administración de fianzas, previniendo un procedimiento ágil para la ejecución y cobro de las garantías que se emitan dentro del esquema.</p>
    </div>

    <h3 class="special-title" style="top:343px">Programa de<br>garantías de fianzas para PyMEs</h3>
    <div class="copy" style="left:29px;top:375px;width:190px">
      <p>Con este programa puedes incrementar la línea de afianzamiento, gracias a que Fondafin aporta 50% de las garantías requeridas en fianzas hasta por 30 millones de pesos</p>
    </div>

    <div class="cta">CALL FOR INFO</div>
    <div class="cta-phone">+52 55 0195 6677</div>
  </div>
</section>

</body>
</html>
```